Business card for Crestline Bathrooms

Please design a business card for our bathroom renovation business. You can use my existing logo, but if you have an idea to modernize it, I would like to see it. Please see attached files first. I would like to use the blue and the orange theme. I like the concept of using the shower head in the logo. Please find following a design (or two) that I have been trying to create with my limited resources. That design was for a sign, but I was going to adopt it and use it as a business card as well. I like the concept of the water splash but I don’t think it “flows” nicely together with the logo. Another thought is that maybe creating the logo out of water splash could work and have a dramatic effect (like the water text and the butterfly picture attached with similar background instead of white). If the above doesn’t work I would like to see a modern simplified design. One of the attached files named as the unwanted business card has all the details that I want included in the business card. Please note that it is two sided.
Updates

I am very thankful for the designs that I have received, but they are very similar and only a couple of attempts to do something with the water splash as per my original brief. Modernizing the logo and having it made out of out of water splash with the orange as color accent could work and have a dramatic effect (like the water text and the butterfly picture attached with similar background instead of white). Please do not use the butterfly itself! This is just an example that images can be created out of water splash.

Contact Information for Business Card

all the details are on the unwonted business card file included

Colors
3176b5

Requirements
Nice to have
• Copied from the brief:
• ... maybe creating the logo out of water splash could work and have a dramatic effect (like the water text and the butterfly picture attached with similar background instead of white). Please do not use the butterfly itself!
Should not have
• I am getting designs with a butterfly. The butterfly picture was an example of creating something from a water splash. The butterfly itself has no association with anything other than the concept of creating a logo out of water splash. Sorry, I thought I was clear in the brief.

```html
<!DOCTYPE html>
<html lang="en">
<head>
<meta charset="utf-8">
<title>Crestline Bathrooms – Business Card</title>
<link rel="stylesheet" href="https://fonts.googleapis.com/css2?family=Roboto:wght@400;500&family=Delius&display=swap">
<style>
  :root {
    --backdrop: #e4e4e4;
    --navy: #1b3055;
    --navy-deep: #14264a;
    --splash-blue: #3e6a9e;
    --splash-foam: #c9d6e4;
    --accent: #ec7b6c;
    --ink: #ffffff;
    --badge: #5d7fb0;
  }
  * { margin: 0; padding: 0; box-sizing: border-box; }
  html, body { width: 1200px; height: 960px; overflow: hidden; }
  body {
    background: var(--backdrop);
    position: relative;
    font-family: "Roboto", Arial, sans-serif;
    color: var(--ink);
  }
  .card {
    position: absolute;
    width: 600px;
    height: 343px;
    background: var(--navy);
    overflow: hidden;
  }
  .card--back { left: 302px; top: 124px; }
  .card--front { left: 299px; top: 493px; }

  .splash {
    position: absolute;
    top: 0;
    height: 100%;
  }
  .card--back .splash {
    left: 0;
    width: 300px;
    background:
      radial-gradient(ellipse 60% 35% at 35% 100%, var(--splash-foam) 0%, rgba(201,214,228,0.35) 45%, transparent 80%),
      radial-gradient(ellipse 55% 80% at 20% 25%, var(--splash-blue) 0%, transparent 75%),
      linear-gradient(90deg, var(--navy-deep) 0%, var(--navy) 100%);
    -webkit-mask-image: linear-gradient(90deg, #000 70%, transparent 100%);
            mask-image: linear-gradient(90deg, #000 70%, transparent 100%);
  }
  .card--front .splash {
    right: 0;
    width: 290px;
    background:
      radial-gradient(ellipse 65% 35% at 65% 100%, var(--splash-foam) 0%, rgba(201,214,228,0.35) 45%, transparent 80%),
      radial-gradient(ellipse 55% 80% at 80% 25%, var(--splash-blue) 0%, transparent 75%),
      linear-gradient(270deg, var(--navy-deep) 0%, var(--navy) 100%);
    -webkit-mask-image: linear-gradient(270deg, #000 70%, transparent 100%);
            mask-image: linear-gradient(270deg, #000 70%, transparent 100%);
  }

  .services {
    position: absolute;
    left: 308px;
    top: 61px;
    list-style: none;
    font-size: 16px;
    line-height: 20px;
  }
  .services li {
    position: relative;
    padding-left: 14px;
    margin-bottom: 8px;
  }
  .services li::before {
    content: "";
    position: absolute;
    left: 0;
    top: 7px;
    width: 6px;
    height: 6px;
    border-radius: 50%;
    background: var(--accent);
  }
  .memberships {
    position: absolute;
    left: 308px;
    top: 244px;
    display: flex;
    align-items: center;
    gap: 16px;
  }
  .memberships .badge { fill: var(--badge); }

  .brand {
    position: absolute;
    left: 111px;
    top: 60px;
    display: flex;
    align-items: center;
    gap: 12px;
  }
  .brand__dot {
    width: 18px;
    height: 18px;
    border-radius: 50%;
    background: var(--accent);
    flex: none;
  }
  .brand__name {
    font-family: "Roboto", Arial, sans-serif;
    font-weight: 500;
    font-size: 30px;
    line-height: 34px;
    color: var(--ink);
  }

  .person {
    position: absolute;
    left: 26px;
    top: 174px;
    font-family: "Delius", "Comic Sans MS", cursive;
    font-size: 24px;
    color: var(--accent);
    letter-spacing: 0.5px;
  }
  .contacts {
    position: absolute;
    left: 27px;
    top: 216px;
    list-style: none;
    font-size: 15.5px;
  }
  .contacts li {
    display: flex;
    align-items: center;
    height: 21px;
  }
  .contacts li:last-child { margin-top: 2px; }
  .contacts svg {
    width: 14px;
    height: 14px;
    margin-right: 10px;
    flex: none;
    fill: var(--accent);
  }
</style>
</head>
<body>

<section class="card card--back" aria-label="Card reverse">
  <div class="splash" role="img" aria-label="Water splash photograph on dark blue"></div>
  <ul class="services">
    <li>Complete Bathroom<br>Renovations &amp; Remodelling</li>
    <li>Professional Service<br>From Concept To Completion</li>
    <li>Highly Skilled &amp;<br>Qualified Tradespeople</li>
    <li>All Work Guaranteed</li>
  </ul>
  <div class="memberships" aria-label="Industry memberships">
    <svg width="30" height="34" viewBox="0 0 30 34" aria-hidden="true"><rect class="badge" x="0" y="0" width="30" height="34" rx="6"/></svg>
    <svg width="112" height="24" viewBox="0 0 112 24" aria-hidden="true"><rect class="badge" x="0" y="0" width="112" height="24" rx="2"/></svg>
  </div>
</section>

<section class="card card--front" aria-label="Card front">
  <div class="splash" role="img" aria-label="Water splash photograph on dark blue"></div>
  <div class="brand">
    <span class="brand__dot"></span>
    <span class="brand__name">Crestline<br>Bathrooms</span>
  </div>
  <p class="person">Daniel Merrow</p>
  <ul class="contacts">
    <li><svg viewBox="0 0 14 14" aria-hidden="true"><path d="M4 0h6a1 1 0 0 1 1 1v12a1 1 0 0 1-1 1H4a1 1 0 0 1-1-1V1a1 1 0 0 1 1-1zm0.8 1.6v9.4h4.4V1.6z"/></svg>0400 555 018</li>
    <li><svg viewBox="0 0 14 14" aria-hidden="true"><path d="M3 0.5l2.2 2.6-1.2 1.7c.8 1.9 2.2 3.4 4.2 4.3l1.6-1.2 2.7 2.2-1.3 2.6C5.6 12.6 1.2 8.2 0.6 2z"/></svg>6200 0147</li>
    <li><svg viewBox="0 0 14 14" aria-hidden="true"><path d="M7 0.5a6.5 6.5 0 1 0 3.6 11.9l-.7-1.1A5.2 5.2 0 1 1 12.2 7c0 1.3-.5 2.1-1.2 2.1-.6 0-.8-.5-.8-1.1V3.8H9v.6A3 3 0 1 0 9.3 9a2 2 0 0 0 1.7 1.3c1.6 0 2.5-1.4 2.5-3.3A6.5 6.5 0 0 0 7 .5zm0 8.3A1.8 1.8 0 1 1 7 5.2a1.8 1.8 0 0 1 0 3.6z"/></svg>daniel@crestlinebathrooms.com.au</li>
    <li><svg viewBox="0 0 14 14" aria-hidden="true"><path d="M7 0.5a6.5 6.5 0 1 0 0 13 6.5 6.5 0 0 0 0-13zm-4.8 7.4l2 .6 1 2-.6 1.4A5.3 5.3 0 0 1 2.2 7.9zm6 4.2l.4-2.2 1.8-1.5-.5-1.8-2.4-.5-1-1.6 1-2a5.3 5.3 0 0 1 .7 9.6z"/></svg>crestlinebathrooms.com.au</li>
    <li><svg viewBox="0 0 14 14" aria-hidden="true"><path d="M0.5 2.5h13v1.2L7 7.8 0.5 3.7zm0 2.6L7 9.2l6.5-4.1v6.4H.5z"/></svg>PO Box 41, Harlow Vale 2600</li>
  </ul>
</section>

</body>
</html>
```